Local Roofing/Construction company business needs new biz card design

We need a new business card design, current cards are from the start of this operation and generic at best. We are a local Construction Company (General Contractor) with a majority of our work originating from insurance claims-exterior finish work is the main focus (Roofs-Siding-Gutters etc). Heavily involved with homeowners and the low ball offers they receive from insurance company's after a insurable event takes place. I have attached some of our original logo file(s) below.

```html
<!DOCTYPE html>
<html lang="en">
<head>
<meta charset="utf-8">
<title>Stonegate Exteriors – Business Card</title>
<link rel="stylesheet" href="https://fonts.googleapis.com/css2?family=Montserrat:wght@300;400;700&display=swap">
<style>
  :root {
    --backdrop: #dfe1e1;
    --paper: #fbfbfa;
    --brand-green: #1f9a3a;
    --text-dark: #2b2b2b;
    --text-muted: #555a58;
  }
  * { margin: 0; padding: 0; box-sizing: border-box; }
  html, body { width: 1200px; height: 829px; overflow: hidden; }
  body {
    background: var(--backdrop);
    font-family: "Montserrat", sans-serif;
    position: relative;
  }
  .card {
    position: absolute;
    top: 264px;
    width: 520px;
    height: 300px;
    background: var(--paper);
    box-shadow: 0 2px 10px rgba(0, 0, 0, 0.12);
  }
  .card--front { left: 60px; }
  .card--back { left: 620px; }

  .name-accent {
    position: absolute;
    left: 0; top: 46px;
    width: 14px; height: 38px;
    background: var(--brand-green);
  }
  .person { position: absolute; left: 32px; top: 46px; }
  .person__name {
    font-weight: 700;
    font-size: 19px;
    letter-spacing: 1.5px;
    color: var(--brand-green);
    text-transform: uppercase;
  }
  .person__title {
    font-weight: 300;
    font-size: 12px;
    color: var(--text-muted);
    margin-top: 2px;
  }

  .brand {
    display: flex;
    align-items: center;
    gap: 8px;
    font-weight: 700;
    color: var(--brand-green);
    text-transform: uppercase;
    letter-spacing: 1px;
  }
  .brand__mark { background: var(--brand-green); flex: none; }
  .card--front .brand {
    position: absolute;
    right: 30px; top: 104px;
    font-size: 16px;
  }
  .card--front .brand__mark { width: 14px; height: 14px; }

  .contact {
    position: absolute;
    left: 250px; top: 168px;
    list-style: none;
    font-size: 12px;
    font-weight: 400;
    color: var(--text-dark);
    line-height: 1.55;
  }
  .contact__address { margin-bottom: 4px; }
  .contact__item { display: flex; align-items: center; gap: 7px; }
  .contact__item svg { width: 10px; height: 10px; fill: var(--brand-green); flex: none; }

  .card--back .brand {
    position: absolute;
    left: 50%; top: 50%;
    transform: translate(-50%, -50%);
    font-size: 24px;
    gap: 12px;
  }
  .card--back .brand__mark { width: 22px; height: 22px; }
</style>
</head>
<body>
  <section class="card card--front" aria-label="Business card front">
    <div class="name-accent"></div>
    <div class="person">
      <p class="person__name">Connor Hale</p>
      <p class="person__title">Managing Director</p>
    </div>
    <div class="brand">
      <span class="brand__mark"></span>
      <span class="brand__name">Stonegate Exteriors</span>
    </div>
    <ul class="contact">
      <li class="contact__address">418 Birchwood Avenue<br>Ashford County 4172</li>
      <li class="contact__item">
        <svg viewBox="0 0 10 10" aria-hidden="true"><path d="M2 0.5 L3.8 0.5 L4.4 3 L3.2 4 Q4.2 6 6 6.8 L7 5.6 L9.5 6.2 L9.5 8 Q9.5 9.5 8 9.5 Q0.5 9 0.5 2 Q0.5 0.5 2 0.5 Z"/></svg>
        0455 217 639
      </li>
      <li class="contact__item">
        <svg viewBox="0 0 10 10" aria-hidden="true"><path d="M0.5 2 H9.5 V8.5 H0.5 Z M0.5 2 L5 5.5 L9.5 2" stroke="#fbfbfa" stroke-width="0.8"/></svg>
        info@stonegateexteriors.com
      </li>
      <li class="contact__item">
        <svg viewBox="0 0 10 10" aria-hidden="true"><circle cx="5" cy="5" r="4.5"/></svg>
        www.stonegateexteriors.com
      </li>
    </ul>
  </section>

  <section class="card card--back" aria-label="Business card back">
    <div class="brand">
      <span class="brand__mark"></span>
      <span class="brand__name">Stonegate Exteriors</span>
    </div>
  </section>
</body>
</html>
```